New web page, 2 companies on the one page

A new web page for an engineering consultancy and maintenance management company

Corlett & Associates is the parent company covering the design and consultancy
Valtrix Engineering is the Maintenance and Reliability company

Target Market(s)

Food & Beverage, ingredients Manufacturing
engineering managers

Coding

Coded - Design and coding required

Number of Pages Required

1 page

Font styles to use
Other font styles liked:
• Roboto

Colors
1861ab
85acd3
d0dfed
cee9f5

```html
<!DOCTYPE html>
<html lang="en">
<head>
<meta charset="utf-8">
<title>Corlett &amp; Associates</title>
<link href="https://fonts.googleapis.com/css2?family=Archivo+Black&family=Lato:wght@400;700&display=swap" rel="stylesheet">
<style>
:root{
  --brand:#1f8ad8;
  --steel:#6f9bd1;
  --band:#6c99cd;
  --navy:#1861ab;
  --ink:#111114;
  --body:#3b3b44;
  --soft:#f3f5fa;
  --footer:#1f1d22;
  --footer-deep:#151318;
  --white:#ffffff;
}
*{box-sizing:border-box;margin:0;padding:0}
html,body{width:1200px;height:3351px;overflow:hidden;background:#fff}
body{font-family:"Lato",sans-serif;color:var(--body)}
.page{position:relative;width:1200px;height:3351px;overflow:hidden}
.abs{position:absolute}
.heading{font-family:"Archivo Black",sans-serif;color:var(--ink);letter-spacing:.5px;line-height:1}
.btn{position:absolute;display:flex;align-items:center;justify-content:center;border-radius:24px;color:#fff;font-weight:700;font-size:16px;background:var(--steel)}
.copy{font-size:13px;line-height:26px;color:var(--body)}

/* hero */
.hero{position:absolute;left:0;top:0;width:1200px;height:628px;background:linear-gradient(100deg,#eef3f8 0%,#dfe8f1 38%,#8da0b6 62%,#4b5466 80%,#6d6e74 100%)}
.brand-mark{position:absolute;display:flex;align-items:center;gap:10px;font-family:"Lato",sans-serif;font-weight:700;font-size:22px;color:var(--navy)}
.brand-mark i{display:block;width:34px;height:34px;border-radius:50%;background:var(--navy)}
.nav a{position:absolute;top:43px;font-size:16px;font-weight:700;color:var(--ink);text-decoration:none}
.nav .active{color:var(--brand);border-bottom:2px solid var(--brand);padding-bottom:3px}
.nav .contact{top:29px;left:928px;width:161px;height:46px;border-radius:23px;background:var(--steel);color:#fff;display:flex;align-items:center;justify-content:center;gap:8px;font-weight:400}
.dots span{position:absolute;top:456px;width:13px;height:13px;border-radius:50%;border:1.5px solid #111}

/* who */
.label-vert{position:absolute;left:121px;top:745px;transform:rotate(-90deg);transform-origin:left top;font-size:12px;color:var(--steel);letter-spacing:1px;width:70px;translate:0 70px}
.photo{position:absolute}

/* offer */
.offer{position:absolute;left:0;top:1150px;width:1200px;height:561px;background:var(--band)}
.card{position:absolute;top:1340px;width:230px;height:249px;background:#fff;border-radius:3px;padding:0 17px}
.card svg{position:absolute;left:17px;top:28px}
.card h3{position:absolute;top:110px;left:17px;font-size:17px;font-weight:700;color:var(--ink);white-space:nowrap}
.card hr{position:absolute;top:143px;left:17px;width:34px;border:0;border-top:2px solid var(--steel)}
.card p{position:absolute;top:160px;left:17px;right:14px;font-size:13px;line-height:20px;color:var(--body)}

/* why */
.why{position:absolute;left:0;top:1711px;width:1200px;height:494px;background:var(--soft)}

/* blog */
.post{position:absolute;top:2435px;width:304px;height:428px;background:#fff;box-shadow:0 2px 8px rgba(0,0,0,.08)}
.post .pic{position:absolute;left:0;top:0;width:304px;height:220px}
.post .date{position:absolute;left:80px;top:200px;width:144px;height:39px;border-radius:20px;background:var(--steel);color:#fff;font-size:14px;display:flex;align-items:center;justify-content:center}
.post h4{position:absolute;left:23px;top:260px;width:260px;font-size:20px;font-weight:400;line-height:26px;color:var(--ink)}
.post p{position:absolute;left:21px;top:322px;width:270px;font-size:13px;line-height:25px}
.post .more{position:absolute;left:21px;top:394px;display:flex;align-items:center;gap:12px;color:var(--navy);font-size:16px;font-weight:700}
.post .more::before{content:"";width:40px;border-top:2px solid var(--navy)}

/* footer */
.footer{position:absolute;left:0;top:2947px;width:1200px;height:349px;background:var(--footer);color:#e8e8ee}
.foot-h{position:absolute;top:3027px;font-size:16px;font-weight:700;color:#fff}
.foot-list{position:absolute;font-size:15px;line-height:26px;color:#e8e8ee}
.field{position:absolute;background:#fff;border-radius:3px;font-size:12px;color:#777;padding:10px 12px}
.social{position:absolute;top:3229px;width:34px;height:34px;border-radius:50%;border:1.5px solid #fff}
.bottom{position:absolute;left:0;top:3296px;width:1200px;height:55px;background:var(--footer-deep);color:#e8e8ee;font-size:13px}
</style>
</head>
<body>
<div class="page">

  <!-- HERO -->
  <section class="hero" role="img" aria-label="Photo of two businessmen meeting at a cafe table with a laptop and coffee"></section>
  <div class="brand-mark" style="left:110px;top:34px"><i></i>Corlett &amp; Associates</div>
  <nav class="nav">
    <a class="active" style="left:399px">HOME</a>
    <a style="left:519px">ABOUT US</a>
    <a style="left:668px">OUR SERVICES</a>
    <a style="left:850px">BLOG</a>
    <a class="contact"><svg width="20" height="20" viewBox="0 0 20 20"><circle cx="10" cy="10" r="9" fill="none" stroke="#fff" stroke-width="1.5"/><circle cx="10" cy="8" r="3" fill="#fff"/><path d="M4.5 16c1.5-3 9.5-3 11 0" fill="#fff"/></svg>CONTACT US</a>
  </nav>
  <h1 class="heading abs" style="left:112px;top:259px;font-size:48px">CORLETT &amp; ASSOCIATES</h1>
  <p class="abs" style="left:112px;top:320px;width:460px;font-size:15px;line-height:25px;color:var(--ink)">Lorem ipsum dolor sit amet, consectetur adipiscing elit, sed do eiusmod tempor incididunt ut labore et dolore magna aliqua.</p>
  <a class="btn" style="left:112px;top:387px;width:154px;height:43px;background:var(--brand)">GET STARTED</a>
  <a class="btn" style="left:276px;top:387px;width:153px;height:43px">LEARN MORE</a>
  <div class="dots"><span style="left:125px;background:#111"></span><span style="left:145px"></span><span style="left:164px"></span><span style="left:183px"></span></div>
  <svg class="abs" style="left:560px;top:604px" width="80" height="26" viewBox="0 0 80 26"><path d="M0 26 L40 0 L80 26 Z" fill="#fff"/><path d="M34 14 L40 20 L46 14" fill="none" stroke="#333" stroke-width="1.5"/></svg>

  <!-- WHO WE ARE -->
  <div class="label-vert">ABOUT US</div>
  <div class="abs" style="left:131px;top:826px;height:69px;border-left:1.5px solid var(--steel)"></div>
  <h2 class="heading abs" style="left:152px;top:740px;font-size:38px">WHO WE ARE</h2>
  <p class="copy abs" style="left:152px;top:794px;width:430px">Lorem ipsum dolor sit amet, consectetur adipiscing elit, sed do eiusmod tempor incididunt ut labore et dolore magna aliqua. Quis isuspendisse ultrices gravida. Risus commodo viverra maecenas accumsan lacus vel facilisis.</p>
  <p class="copy abs" style="left:152px;top:911px;width:430px">Lorem ipsum dolor sit amet, consectetur adipiscing elit, sed do eiusmod tempor incididunt ut labore et dolore magna aliqua. Quis isuspendisse ultrices gravida.</p>
  <a class="btn" style="left:152px;top:1013px;width:153px;height:43px">LEARN MORE</a>
  <div class="photo" style="left:728px;top:705px;width:360px;height:331px;background:linear-gradient(135deg,#cfcfcf,#6f6f6f)" role="img" aria-label="Black and white photo of an office meeting"></div>
  <div class="photo" style="left:685px;top:748px;width:356px;height:345px;border:5px solid var(--steel)"></div>
  <div class="photo" style="left:654px;top:780px;width:359px;height:286px;background:linear-gradient(135deg,#b7b3ad,#6b655f 55%,#3e3a37)" role="img" aria-label="Photo of colleagues shaking hands across a meeting table"></div>

  <!-- WHAT WE OFFER -->
  <section class="offer"></section>
  <h2 class="heading abs" style="left:0;width:1200px;text-align:center;top:1212px;font-size:38px;color:#fff">WHAT WE OFFER</h2>
  <p class="abs" style="left:0;width:1200px;text-align:center;top:1255px;font-size:16px;line-height:26px;color:#fff">Lorem ipsum dolor sit amet, consectetur adipiscing elit, sed do eiusmod<br>tempor incididunt ut labore et dolore magna aliqua</p>

  <div class="card" style="left:112px">
    <svg width="66" height="66" viewBox="0 0 66 66" fill="none" stroke="var(--steel)" stroke-width="2"><rect x="4" y="4" width="58" height="38"/><circle cx="20" cy="22" r="9"/><path d="M20 13v9h9M36 14h20M36 22h20M36 30h14M16 42v12M50 42v12M8 54h50M12 62h10M44 62h10"/></svg>
    <h3>Process &amp; Facilities Design</h3><hr>
    <p>Sed ut perspiciatis unde omnis iste natus error sit voluptatem accusantium dolore</p>
  </div>
  <div class="card" style="left:360px">
    <svg width="66" height="66" viewBox="0 0 66 66" fill="none" stroke="var(--steel)" stroke-width="2"><rect x="4" y="4" width="44" height="52"/><path d="M12 14h28M12 22h20M12 30h16M12 38h12"/><circle cx="48" cy="48" r="10"/><circle cx="48" cy="48" r="4"/><path d="M48 34v4M48 58v4M34 48h4M58 48h4"/></svg>
    <h3>Project Management</h3><hr>
    <p>Sed ut perspiciatis unde omnis iste natus error sit voluptatem accusantium dolore</p>
  </div>
  <div class="card" style="left:610px">
    <svg width="66" height="66" viewBox="0 0 66 66" fill="none" stroke="var(--steel)" stroke-width="2"><circle cx="33" cy="30" r="22"/><circle cx="33" cy="30" r="14"/><path d="M28 22l5 5 5-5M33 27v26M26 44h14"/></svg>
    <h3>Maintenance Execution</h3><hr>
    <p>Sed ut perspiciatis unde omnis iste natus error sit voluptatem accusantium dolore</p>
  </div>
  <div class="card" style="left:858px">
    <svg width="76" height="66" viewBox="0 0 76 66" fill="none" stroke="var(--steel)" stroke-width="2"><rect x="4" y="8" width="18" height="16" rx="5"/><path d="M28 12h44M28 22h44M28 36h44M28 46h44"/><path d="M2 40c6-8 18-8 24 0c-6 8-18 8-24 0z"/><circle cx="14" cy="40" r="3"/></svg>
    <h3>Vision Inspection Systems</h3><hr>
    <p>Sed ut perspiciatis unde omnis iste natus error sit voluptatem accusantium dolore</p>
  </div>
  <a class="btn" style="left:523px;top:1615px;width:205px;height:43px;background:transparent;border:1.5px solid #fff;font-weight:400">VIEW ALL SERVICES</a>

  <!-- WHY CHOOSE US -->
  <section class="why"></section>
  <div class="abs" style="left:546px;top:1711px;width:654px;height:494px;background:linear-gradient(90deg,var(--soft) 0%,#d9dde3 22%,#9aa0a8 55%,#5a5d63 80%,#c9ccd1 100%)" role="img" aria-label="Photo of a thoughtful man in glasses working at a laptop"></div>
  <div class="heading abs" style="left:140px;top:1776px;font-size:30px;color:#dfe2e8">WHY CHOOSE US?</div>
  <h2 class="heading abs" style="left:112px;top:1818px;font-size:40px">CORLETT &amp; ASSOCIATES</h2>
  <p class="copy abs" style="left:112px;top:1868px;width:430px">Lorem ipsum dolor sit amet, consectetur adipiscing elit, sed do eiusmod tempor incididunt ut labore et dolore magna aliqua. Quis isuspendisse ultrices gravida. Risus commodo viverra maecenas accumsan lacus vel facilisis.</p>
  <p class="copy abs" style="left:112px;top:1985px;width:430px">Lorem ipsum dolor sit amet, consectetur adipiscing elit, sed do eiusmod tempor incididunt ut labore et dolore magna aliqua. Quis isuspendisse ultrices gravida.</p>
  <a class="btn" style="left:112px;top:2080px;width:154px;height:43px">LEARN MORE</a>

  <!-- LATEST BLOG -->
  <h2 class="heading abs" style="left:0;width:1200px;text-align:center;top:2304px;font-size:40px;letter-spacing:3px">LATEST BLOG</h2>
  <p class="abs" style="left:0;width:1200px;text-align:center;top:2353px;font-size:16px;line-height:26px;color:var(--ink)">Lorem ipsum dolor sit amet, consectetur adipiscing elit, sed do eiusmod<br>tempor incididunt ut labore et dolore magna aliqua</p>

  <article class="post" style="left:112px">
    <div class="pic" style="background:linear-gradient(135deg,#4a5c78,#8a94a4 50%,#2c3446)" role="img" aria-label="Photo of two engineers inspecting machinery"></div>
    <div class="date">MAY 21, 2019</div>
    <h4>The standard Lorem Ipsum passage, use the 1500s</h4>
    <p>Lorem ipsum dolor sit amet, tetur adipiscing elit, sed do eiusmod tempor indunt ut labore et dolore magna aliqua. Ut enim ad</p>
    <div class="more">Read More</div>
  </article>
  <article class="post" style="left:447px">
    <div class="pic" style="background:linear-gradient(135deg,#b88a4a,#ddd2c2 50%,#6a6a70)" role="img" aria-label="Photo of a hand drawing plans next to a laptop"></div>
    <div class="date">MAR 2, 2021</div>
    <h4>The standard Lorem Ipsum passage, use the 1500s</h4>
    <p>Lorem ipsum dolor sit amet, tetur adipiscing elit, sed do eiusmod tempor indunt ut labore et dolore magna aliqua. Ut enim ad</p>
    <div class="more">Read More</div>
  </article>
  <article class="post" style="left:784px">
    <div class="pic" style="background:linear-gradient(135deg,#5c6a74,#a4a8ac 50%,#8a3a34)" role="img" aria-label="Photo of two technicians at a laptop in a workshop"></div>
    <div class="date">JAN 4, 2021</div>
    <h4>The standard Lorem Ipsum passage, use the 1500s</h4>
    <p>Lorem ipsum dolor sit amet, tetur adipiscing elit, sed do eiusmod tempor indunt ut labore et dolore magna aliqua. Ut enim ad</p>
    <div class="more">Read More</div>
  </article>

  <!-- FOOTER -->
  <footer class="footer"></footer>
  <div class="brand-mark" style="left:108px;top:3044px;color:#fff;font-size:24px"><i style="background:var(--brand)"></i>Corlett &amp; Associates</div>
  <div class="brand-mark" style="left:108px;top:3142px;color:#fff;font-size:24px"><i style="background:var(--brand)"></i>Valtrix Engineering</div>
  <span class="social" style="left:157px" aria-label="Social link"></span>
  <span class="social" style="left:201px" aria-label="Social link"></span>
  <span class="social" style="left:245px" aria-label="Social link"></span>
  <span class="social" style="left:288px" aria-label="Social link"></span>

  <div class="foot-h" style="left:424px">QUICK LINKS</div>
  <div class="foot-list" style="left:424px;top:3051px">Home<br>About us<br>Our services<br>Blog<br>Contact Us</div>

  <div class="foot-h" style="left:572px">CONTACT INFO</div>
  <div class="foot-list" style="left:572px;top:3051px;width:210px;line-height:21px">
    <div style="display:flex;gap:8px"><svg width="10" height="14" viewBox="0 0 10 14" style="margin-top:4px;flex:none"><path d="M5 0a5 5 0 0 0-5 5c0 4 5 9 5 9s5-5 5-9a5 5 0 0 0-5-5z" fill="var(--steel)"/><circle cx="5" cy="5" r="2" fill="var(--footer)"/></svg><span>123 Avenue name, City name 10150, United States</span></div>
    <div style="display:flex;gap:8px;margin-top:10px;align-items:center"><svg width="11" height="11" viewBox="0 0 24 24"><path d="M6.6 10.8a15 15 0 0 0 6.6 6.6l2.2-2.2a1 1 0 0 1 1-.3 11 11 0 0 0 3.6.6 1 1 0 0 1 1 1V20a1 1 0 0 1-1 1A17 17 0 0 1 3 4a1 1 0 0 1 1-1h3.5a1 1 0 0 1 1 1 11 11 0 0 0 .6 3.6 1 1 0 0 1-.3 1z" fill="var(--steel)"/></svg>888-888-8888</div>
    <div style="display:flex;gap:8px;margin-top:10px;align-items:center"><svg width="11" height="9" viewBox="0 0 11 9"><rect width="11" height="9" fill="var(--steel)"/><path d="M0 0l5.5 5L11 0" fill="none" stroke="var(--footer)"/></svg>info@brayfordcontracting.com</div>
  </div>

  <div class="foot-h" style="left:816px">CONTACT US</div>
  <p class="abs" style="left:816px;top:3055px;font-size:12.5px;line-height:21px;color:#e8e8ee">Want more information about Brayford Contracting?<br>Want a quote on an upcoming project?</p>
  <div class="field" style="left:816px;top:3110px;width:139px;height:35px">Name</div>
  <div class="field" style="left:963px;top:3110px;width:138px;height:35px">Email</div>
  <div class="field" style="left:816px;top:3155px;width:285px;height:55px">Message</div>
  <a class="btn" style="left:819px;top:3219px;width:127px;height:40px;font-size:15px;gap:8px">SUBMIT <svg width="22" height="10" viewBox="0 0 22 10"><path d="M0 5h20M16 1l4 4-4 4" fill="none" stroke="#fff" stroke-width="1.5"/></svg></a>

  <div class="bottom">
    <span class="abs" style="left:113px;top:19px">Copyright © 2021 CORLETT &amp; ASSOCIATES. All Rights Reserved.</span>
    <span class="abs" style="left:842px;top:19px">Terms and Conditions &nbsp;&nbsp;|&nbsp;&nbsp; Privacy Policy</span>
  </div>
</div>
</body>
</html>
```